Unique Business Card Design

Unique Business Card design for our orthotic and prosthetic company. Our logo is on our website, color is light blue. Unique shape (artificial leg shaped, vertical, etc..) preferred. Logo, business name, individual name and basic demographics needed.

Industry/Entity Type

Business

Contact Information for Business Card

Logo, Industry, Phone # Logo, "Prosthetic & Orthotic Services" Place to add individual name and contact info

Colors
cee9f5

Requirements
Must have
• The icon must be there, placement of "Prosthetic & Orthotic Services" can be moved
Nice to have
• Like the mix of light blue, and a little darker blue. One design included the icons from my website which was a nice touch

```html
<!DOCTYPE html>
<html lang="en">
<head>
<meta charset="utf-8">
<title>Limbworks Co. – Business Card</title>
<link rel="stylesheet" href="https://fonts.googleapis.com/css2?family=Source+Sans+3:wght@400;600;700&family=Crimson+Text:ital@1&display=swap">
<style>
  :root {
    --backdrop: #2b2a28;
    --navy: #1c2d6b;
    --navy-deep: #13204d;
    --panel-top: #3a4a78;
    --panel-bottom: #16224f;
    --silver-light: #f3f0ea;
    --silver-mid: #d9d4cb;
    --silver-dark: #c9c3b8;
    --disc: #d8d2c6;
    --ink: #2a2a2a;
  }
  * { margin: 0; padding: 0; box-sizing: border-box; }
  html, body { width: 1200px; height: 834px; overflow: hidden; }
  body {
    background: var(--backdrop);
    font-family: "Source Sans 3", "Helvetica Neue", Arial, sans-serif;
    position: relative;
  }
  .card {
    position: absolute;
    left: 295px; top: 207px;
    width: 727px; height: 413px;
    border-radius: 14px;
    overflow: hidden;
    background: linear-gradient(135deg, var(--silver-light) 0%, var(--silver-mid) 55%, var(--silver-dark) 100%);
  }
  .card__band {
    position: absolute; left: 0; top: 0;
    width: 258px; height: 100%;
    background: linear-gradient(160deg, var(--panel-top) 0%, var(--panel-bottom) 100%);
  }
  .card__disc {
    position: absolute;
    left: 26px; top: 108px;
    width: 200px; height: 200px;
    border-radius: 50%;
    background: var(--disc);
  }
  .card__info {
    position: absolute; left: 302px; top: 0; right: 20px; height: 100%;
    color: var(--ink);
  }
  .person-name {
    position: absolute; top: 24px;
    font-size: 23px; font-weight: 700; color: var(--navy);
    white-space: nowrap;
  }
  .person-name .credentials { font-size: 17px; font-weight: 600; }
  .person-email { position: absolute; top: 57px; font-size: 18px; }
  .address { position: absolute; top: 88px; font-size: 18px; line-height: 27px; font-style: normal; }
  .brand-name {
    position: absolute; top: 158px;
    font-size: 40px; font-weight: 600; color: var(--navy);
    letter-spacing: 0.5px; white-space: nowrap;
  }
  .brand-rule {
    position: absolute; top: 208px; left: 0; width: 324px; height: 3px;
    background: var(--navy);
  }
  .tagline {
    position: absolute; top: 216px; left: 18px;
    font-family: "Crimson Text", Georgia, serif;
    font-style: italic; font-size: 21px; color: var(--navy-deep);
    white-space: nowrap;
  }
  .contact-list { position: absolute; top: 272px; list-style: none; }
  .contact-list li {
    display: flex; align-items: center; gap: 9px;
    height: 29px; font-size: 18px;
  }
  .contact-list svg { width: 20px; height: 20px; fill: var(--navy); flex: none; }
</style>
</head>
<body>
  <article class="card">
    <div class="card__band">
      <div class="card__disc"></div>
    </div>
    <div class="card__info">
      <h1 class="person-name">Mirela Ostrander<span class="credentials">, CO LPO</span></h1>
      <p class="person-email">Mostrander@limbworksco.com</p>
      <address class="address">2380 W. 14th St.<br>Fairhaven, NY 11990</address>
      <p class="brand-name">LIMBWORKS CO.</p>
      <div class="brand-rule"></div>
      <p class="tagline">Prosthetic &amp; Orthotic Services</p>
      <ul class="contact-list">
        <li><svg viewBox="0 0 24 24" aria-hidden="true"><path d="M6.6 10.8a15.1 15.1 0 0 0 6.6 6.6l2.2-2.2c.3-.3.7-.4 1-.2 1.1.4 2.3.6 3.6.6.6 0 1 .4 1 1V20c0 .6-.4 1-1 1A17 17 0 0 1 3 4c0-.6.4-1 1-1h3.5c.6 0 1 .4 1 1 0 1.3.2 2.5.6 3.6.1.3 0 .7-.2 1z"/></svg>555.014.2200</li>
        <li><svg viewBox="0 0 24 24" aria-hidden="true"><path d="M7 3h10v4H7zM4 8h16a2 2 0 0 1 2 2v6h-4v5H6v-5H2v-6a2 2 0 0 1 2-2zm4 8v3h8v-3z"/></svg>555.014.2201</li>
        <li><svg viewBox="0 0 24 24" aria-hidden="true"><path d="M7 1h10a2 2 0 0 1 2 2v18a2 2 0 0 1-2 2H7a2 2 0 0 1-2-2V3a2 2 0 0 1 2-2zm0 3v15h10V4z"/></svg>555-017-3846</li>
        <li><svg viewBox="0 0 24 24" aria-hidden="true"><path d="M12 2a10 10 0 1 0 0 20 10 10 0 0 0 0-20zm-1 17.9A8 8 0 0 1 4.2 10L9 14.8v1a2 2 0 0 0 2 2zm6.9-2.5a2 2 0 0 0-1.9-1.4h-1v-3a1 1 0 0 0-1-1H8v-2h2a1 1 0 0 0 1-1V7h2a2 2 0 0 0 2-2v-.4a8 8 0 0 1 2.9 12.8z"/></svg>www.limbworksco.com</li>
      </ul>
    </div>
  </article>
</body>
</html>
```